indépendant en tant que Massothérapeute et Préparateur Mental, j'ai besoin de ...

Massothérapeute et préparateur mental indépendant, je recherche une carte de visite sobre et dynamique, sans images liées au massage ou à la préparation mentale mais intégrant mon logo. Les couleurs que j'aime bien sont : Blanc, gris, anthracite, noir et jaune

Contact Information for Business Card

carte de préférence Horizontale
neutre qui puisse toucher le deux domaines Massothérapie et préparation mentale

Requirements
Must have
• mon projet doit intégrer au recto:
LOGO
Loïc Bardèze
078 513 26 48
info@loicbardeze.ch
et éventuellement www.loicbardeze.ch

et au verso les deux adresses:

Chemin des Ormilles 7B
1400 Yverdon-les-Bains

Route de la Gravière 9
1700 Fribourg

Should not have
• mon projet ne doit pas contenir d'image en liens avec le massage ni la préparation mentale.

```html
<!DOCTYPE html>
<html lang="fr">
<head>
<meta charset="utf-8">
<title>Loïc Bardèze – Cartes de visite</title>
<link href="https://fonts.googleapis.com/css2?family=Lato:wght@400;700&display=swap" rel="stylesheet">
<style>
  :root {
    --bg: #e4e4e4;
    --yellow: #ebe56c;
    --white: #ffffff;
    --black: #000000;
    --rule: #d9d9d9;
  }
  * { margin: 0; padding: 0; box-sizing: border-box; }
  html, body {
    width: 1200px; height: 801px; overflow: hidden;
    background: var(--bg);
    font-family: "Lato", sans-serif;
  }
  .canvas { position: relative; width: 1200px; height: 801px; }

  /* Address side */
  .card-addresses {
    position: absolute; left: 354px; top: 46px;
    width: 517px; height: 309px;
    background: var(--yellow);
  }
  .card-addresses .inner {
    position: absolute; left: 21px; top: 21px; right: 21px; bottom: 21px;
    background: var(--white);
  }
  .brand-name {
    position: absolute; right: 305px; top: 143px;
    font-weight: 700; font-size: 15px; color: var(--black);
    white-space: nowrap;
  }
  .address-block {
    position: absolute; left: 232px; top: 78px; width: 180px;
    color: var(--black);
  }
  .address-block h2 {
    font-size: 13px; font-weight: 700; letter-spacing: 2.2px;
    padding-bottom: 6px; border-bottom: 1px solid var(--rule);
    margin-bottom: 13px;
  }
  .address-block p { font-size: 11.5px; line-height: 16px; letter-spacing: 0.2px; }
  .address-block .divider {
    width: 15px; height: 1px; background: var(--black);
    margin: 7px 0 8px;
  }

  /* Contact side */
  .card-contact {
    position: absolute; left: 354px; top: 424px;
    width: 514px; height: 309px;
    background: var(--white);
  }
  .card-contact .corner { position: absolute; left: 0; top: 0; }
  .card-contact .inner {
    position: absolute; left: 22px; top: 22px;
    width: 470px; height: 265px;
    background: var(--black); color: var(--white);
  }
  .person-name {
    position: absolute; left: 21px; top: 165px;
    font-size: 19px; font-weight: 400; letter-spacing: 0.6px;
  }
  .contact-list {
    position: absolute; left: 23px; top: 204px;
    list-style: none; font-size: 13px; letter-spacing: 0.4px;
  }
  .contact-list li { line-height: 22px; }
  .contact-list b { font-weight: 700; }
  .brand-lockup {
    position: absolute; right: 22px; top: 214px;
    display: flex; align-items: center; gap: 8px;
    font-size: 16px; font-weight: 700; color: var(--white);
  }
  .brand-lockup .mark { width: 10px; height: 10px; background: var(--white); }
</style>
</head>
<body>
<div class="canvas">

  <section class="card-addresses">
    <div class="inner">
      <div class="brand-name">Loïc Bardèze</div>
      <div class="address-block">
        <h2>ADRESSES</h2>
        <p>Chemin des Ormilles 7B<br>1400 Yverdon-les-Bains</p>
        <div class="divider"></div>
        <p>Route de la Gravière 9<br>1700 Fribourg</p>
      </div>
    </div>
  </section>

  <section class="card-contact">
    <svg class="corner" width="70" height="68" viewBox="0 0 70 68" aria-hidden="true">
      <polygon points="0,0 70,0 0,68" fill="var(--yellow)"/>
    </svg>
    <div class="inner">
      <h1 class="person-name">LOÏC BARDÈZE</h1>
      <ul class="contact-list">
        <li><b>M</b> : 078 513 26 48</li>
        <li><b>E</b>&nbsp;&nbsp;: info@loicbardeze.ch</li>
        <li><b>W</b> : www.loicbardeze.ch</li>
      </ul>
      <div class="brand-lockup"><span class="mark"></span>Loïc Bardèze</div>
    </div>
  </section>

</div>
</body>
</html>
```